CrestHornSupply.com

I need a new webdesign for a company in the San Jose/SF Bay area that showcases the financial benefits of buying used band instruments for junior high students.This would be opposed to the current and costly option of renting cheap quality instruments from the 2 or 3 local music stores that charge a monthly fee that over the years charges the buyer 3 or 4x over..
Instruments: focus in on Alto Sax, Trumpet, Flute, Clarinet, Trombone, Tenor Sax, Baritone
Target middle schools are Larkfield Middle School and Maple Middle School in San Jose, CA. Both have award winning band programs.
Files attached may or may not be important.
Tabs Needed and funtional
Contact
Shopping Cart
Select Instrument
Checkout
Add to Cart, etc.
Instuments
quantity, etc.
trade in your instrument/sell your instrument
ability to add or take away new instruments for sale. including pictures
Additional questions or info, feel free to ask
Updates
Hi Designers,
Project Deadline Extended
Reason: In the next week you will be receiving specific content that will be required to be had on the website.
New desigins are still welcome. Please continue to contact me if you have questions about your individual designs.
Thanks!
Crest Horn

```html
<!DOCTYPE html>
<html lang="en">
<head>
<meta charset="utf-8">
<title>Cadenza Instrument Store – Checkout</title>
<link href="https://fonts.googleapis.com/css2?family=Lato:wght@300;400;700;900&family=Roboto:wght@400;500;700&family=Roboto+Condensed:wght@700&display=swap" rel="stylesheet">
<style>
  :root{
    --page:#eeeeee;
    --white:#ffffff;
    --ink:#111111;
    --text:#333333;
    --muted:#666666;
    --rule:#dddddd;
    --green:#4a8f72;
    --footer:#000000;
    --footer-text:#8a8a8a;
    --footer-rule:#2a2a2a;
    --tweet:#6fc7cf;
    --field:#333333;
    --social:#1e1e1e;
  }
  *{box-sizing:border-box;margin:0;padding:0}
  html,body{width:1200px;height:1000px;overflow:hidden}
  body{background:var(--page);font-family:'Roboto',Arial,sans-serif;color:var(--text);position:relative}
  .site{position:absolute;left:150px;top:0;width:900px;height:1000px;background:var(--white)}
  .abs{position:absolute}

  /* header */
  .account-links{left:14px;top:13px;font-size:10px;display:flex;gap:10px;color:var(--text)}
  .account-links span+span{border-left:1px solid var(--rule);padding-left:10px}
  .currency{right:14px;top:13px;font-size:10px}
  .brand{left:295px;top:38px;width:310px;height:60px}
  .brand-tag{position:absolute;right:0;top:4px;font-family:'Lato',sans-serif;font-weight:700;font-size:9px;line-height:11px;letter-spacing:1px;color:var(--ink)}
  .brand-name{position:absolute;left:0;right:0;top:16px;text-align:center;font-family:'Lato',sans-serif;font-weight:900;font-size:46px;line-height:46px;color:var(--ink);letter-spacing:1px}

  /* nav */
  .navbar{left:0;top:131px;width:900px;height:46px;border-top:1px solid var(--rule);border-bottom:4px solid var(--ink)}
  .search{left:0;top:0;width:180px;height:42px;border-right:1px solid var(--rule);display:flex;align-items:center;padding-left:18px;gap:9px;font-size:10px}
  .menu{left:180px;top:0;width:540px;height:42px}
  .menu a{position:absolute;top:12px;font-family:'Lato',sans-serif;font-weight:700;font-size:15px;color:var(--ink);text-decoration:none;display:flex;align-items:center;gap:5px}
  .menu a.current{color:#888}
  .cart{left:720px;top:0;width:180px;height:42px;border-left:1px solid var(--rule);display:flex;align-items:center;padding-left:14px;gap:10px;font-size:11px}

  /* title */
  .crumbs{left:14px;top:192px;font-size:9px;font-weight:700;color:var(--text)}
  .page-title{left:13px;top:202px;font-family:'Lato',sans-serif;font-weight:300;font-size:31px;color:var(--ink)}
  .title-rule{left:0;top:250px;width:900px;border-top:1px solid var(--rule)}
  .col-rule{left:450px;top:251px;height:307px;border-left:1px solid var(--rule)}

  /* forms */
  .panel-head{font-family:'Lato',sans-serif;font-weight:700;font-size:15px;color:var(--ink)}
  .label{font-size:9.5px;color:var(--text)}
  .label b{color:#d33;font-weight:400}
  .field{width:293px;height:23px;border:1px solid #ccc;border-radius:3px;background:var(--white);box-shadow:inset 0 1px 2px rgba(0,0,0,.08)}
  .btn{height:25px;border-radius:13px;background:var(--green);color:var(--white);font-size:11px;font-weight:700;display:flex;align-items:center;justify-content:center}
  .link{font-size:9px;color:var(--green)}
  .note{font-size:9px;color:var(--text)}

  /* footer */
  .footer{left:0;top:558px;width:900px;height:442px;background:var(--footer);color:var(--footer-text)}
  .f-head{font-size:11px;font-weight:700;color:var(--white)}
  .post-title{width:285px;font-size:11px;font-weight:700;color:var(--white);line-height:14px}
  .post-body{width:300px;font-size:9px;line-height:12px}
  .post-meta{font-size:9.5px;display:flex;align-items:center;gap:6px}
  .post-meta b{color:var(--white);font-weight:500}
  .tweet{width:305px;font-size:9px;line-height:12px}
  .tweet em{font-style:normal;color:var(--tweet)}
  .ago{font-size:9px}
  .contact-text{width:250px;font-size:9px;line-height:12px}
  .contact-text b{color:var(--white);font-weight:400}
  .social{width:26px;height:26px;border-radius:50%;background:var(--social);display:flex;align-items:center;justify-content:center}
  .news-head{font-family:'Roboto Condensed',sans-serif;font-weight:700;font-size:14px;letter-spacing:.5px;color:var(--white)}
  .news-field{width:240px;height:27px;border-radius:3px;background:var(--field);color:var(--white);font-size:9px;display:flex;align-items:center;justify-content:space-between;padding:0 9px}
  .bottom-rule{left:0;top:359px;width:900px;border-top:1px solid var(--footer-rule)}
  .copyright{left:14px;top:383px;font-size:9px}
  .footer-links{right:14px;top:383px;font-size:9px;color:var(--white);display:flex;gap:9px}
</style>
</head>
<body>
<div class="site">
  <header>
    <div class="abs account-links"><span>Login</span><span>Register</span></div>
    <div class="abs currency">$ - USD &#8964;</div>
    <div class="abs brand">
      <div class="brand-tag">INSTRUMENT STORE</div>
      <div class="brand-name">Cadenza</div>
    </div>
    <nav class="abs navbar">
      <div class="abs search">
        <svg width="16" height="16" viewBox="0 0 16 16" fill="none" stroke="#333" stroke-width="1.3"><circle cx="9.5" cy="6.5" r="5"/><path d="M6 10L1.5 14.5"/></svg>
        <span>Search</span>
      </div>
      <div class="abs menu">
        <a style="left:54px">HOME</a>
        <a class="current" style="left:146px">SHOP <svg width="7" height="5"><path d="M.5 .5L3.5 3.5 6.5 .5" fill="none" stroke="#888"/></svg></a>
        <a style="left:234px">SALE <svg width="7" height="5"><path d="M.5 .5L3.5 3.5 6.5 .5" fill="none" stroke="#555"/></svg></a>
        <a style="left:318px">BLOG</a>
        <a style="left:405px">CONTACT US</a>
      </div>
      <div class="abs cart">
        <svg width="18" height="16" viewBox="0 0 18 16" fill="none" stroke="#333" stroke-width="1.1"><path d="M.5 1.5h3l2.5 9h9l2-6.5H5"/><circle cx="7" cy="13.5" r="1.3"/><circle cx="14" cy="13.5" r="1.3"/></svg>
        <span>3 ITEMS - $150.00</span>
      </div>
    </nav>
  </header>

  <main>
    <div class="abs crumbs">HOME » CHECKOUT</div>
    <h1 class="abs page-title">Checkout</h1>
    <div class="abs title-rule"></div>
    <div class="abs col-rule"></div>

    <section class="customer-login">
      <h2 class="abs panel-head" style="left:14px;top:282px">CUSTOMER LOGIN</h2>
      <div class="abs label" style="left:14px;top:311px">Email Address <b>*</b></div>
      <div class="abs field" style="left:15px;top:329px"></div>
      <div class="abs label" style="left:14px;top:360px">Password <b>*</b></div>
      <div class="abs field" style="left:15px;top:378px"></div>
      <div class="abs btn" style="left:15px;top:417px;width:67px">Login</div>
      <div class="abs link" style="left:14px;top:450px">Forgot your password ?</div>
      <div class="abs note" style="left:14px;top:466px">or <span class="link">Return to Store</span></div>
    </section>

    <section class="guest-login">
      <h2 class="abs panel-head" style="left:464px;top:282px">GUEST LOGIN</h2>
      <div class="abs note" style="left:464px;top:312px">Continue checkout as a guest. No sign-up required.</div>
      <div class="abs btn" style="left:465px;top:417px;width:115px">Contiune as Guest</div>
    </section>
  </main>

  <footer class="abs footer">
    <div class="abs f-head" style="left:14px;top:32px">LATEST FROM BLOG</div>
    <div class="abs post-title" style="left:14px;top:65px">Neque porro quisquam est, qui dolorem ipsum dolars vin quia dolor sit amet</div>
    <div class="abs post-body" style="left:14px;top:104px">Ut enim ad minima veniam, quis nostrum exercitationem ullam corporis suscipit laboriosam, nisi ut aliquid ex ea commodi consequatur? Quis autem vel eum iure reprehenderit qui in ea voluptate ..</div>
    <div class="abs post-meta" style="left:14px;top:155px">
      <svg width="14" height="14" viewBox="0 0 14 14" fill="none" stroke="#aaa"><circle cx="7" cy="4.5" r="3.5"/><path d="M1 13.5c0-3.5 2.7-5 6-5s6 1.5 6 5z"/></svg><b>Admin</b>
      <span style="width:17px"></span>
      <svg width="14" height="13" viewBox="0 0 14 13" fill="none" stroke="#aaa"><path d="M7 1C3.7 1 1 3 1 5.5c0 1.4.8 2.6 2 3.4L2.5 12l3.2-2c.4.1.9.1 1.3.1 3.3 0 6-2 6-4.5S10.3 1 7 1z"/></svg><span>20 comments</span>
    </div>
    <div class="abs" style="left:14px;top:195px;width:45px;border-top:1px solid #444"></div>
    <div class="abs post-title" style="left:14px;top:215px">Illum qui dolorem eum fugiat quo voluptas impress</div>
    <div class="abs post-body" style="left:14px;top:240px">Ut enim ad minima veniam, quis nostrum exercitationem ullam corporis suscipit laboriosam, nisi ut aliquid ex ea commodi consequatur? Quis autem vel eum iure reprehenderit qui in ea voluptate ..</div>
    <div class="abs post-meta" style="left:14px;top:292px">
      <svg width="14" height="14" viewBox="0 0 14 14" fill="none" stroke="#aaa"><circle cx="7" cy="4.5" r="3.5"/><path d="M1 13.5c0-3.5 2.7-5 6-5s6 1.5 6 5z"/></svg><b>Admin</b>
      <span style="width:17px"></span>
      <svg width="14" height="13" viewBox="0 0 14 13" fill="none" stroke="#aaa"><path d="M7 1C3.7 1 1 3 1 5.5c0 1.4.8 2.6 2 3.4L2.5 12l3.2-2c.4.1.9.1 1.3.1 3.3 0 6-2 6-4.5S10.3 1 7 1z"/></svg><span>20 comments</span>
    </div>

    <div class="abs" style="left:331px;top:28px;width:20px;height:20px;border-radius:50%;background:var(--tweet)"></div>
    <div class="abs f-head" style="left:358px;top:32px">LATEST TWEETS</div>
    <div class="abs tweet" style="left:329px;top:66px"><em>@Admin @User</em> Ut enim ad minima veniam, quis nostrum exercitationem suscipit laboriosam, nisi ut aliquid ex ea commodi consequatur?</div>
    <div class="abs ago" style="left:329px;top:102px">9 hours ago</div>
    <div class="abs tweet" style="left:329px;top:144px"><em>@Admin</em> Ut enim ad minima veniam, quis nostrum exercitationem due suscipit laboriosam, nisi ut aliquid ex ea commodi consequatur?</div>
    <div class="abs ago" style="left:329px;top:180px">9 hours ago</div>
    <div class="abs tweet" style="left:329px;top:221px"><em>@Admin</em> Ut enim ad minima veniam, quis nostrum exercitationem</div>
    <div class="abs ago" style="left:329px;top:245px">9 hours ago</div>

    <div class="abs f-head" style="left:644px;top:32px">CONTACT US</div>
    <div class="abs contact-text" style="left:644px;top:66px">Sed ut perspiciatis unde omnis iste natus error sit volupt accusantium doloremque laudantium, totam rem aperiam, eaque ipsa quae ab illo inventore veritatis.</div>
    <div class="abs contact-text" style="left:644px;top:113px">Phone: 01 234 567<br>Email: <b>hello@cadenzamusic.com</b></div>
    <div class="abs social" style="left:644px;top:159px"></div>
    <div class="abs social" style="left:676px;top:159px"></div>
    <div class="abs social" style="left:708px;top:159px"><svg width="10" height="10" viewBox="0 0 10 10" fill="none" stroke="#fff" stroke-width="1.3"><circle cx="1.8" cy="8.2" r=".9" fill="#fff" stroke="none"/><path d="M1 4.5a4.5 4.5 0 014.5 4.5M1 1a8 8 0 018 8"/></svg></div>
    <div class="abs social" style="left:740px;top:159px"><svg width="11" height="8" viewBox="0 0 11 8" fill="#fff"><path d="M0 0h11L5.5 4.3z"/><path d="M0 1.2v6.8h11V1.2L5.5 5.6z"/></svg></div>
    <div class="abs news-head" style="left:644px;top:222px">NEWSLETTERS</div>
    <div class="abs contact-text" style="left:644px;top:259px">We promise to only send you good things.</div>
    <div class="abs news-field" style="left:644px;top:282px"><span>Enter your email address</span><svg width="12" height="9" viewBox="0 0 12 9" fill="none" stroke="#fff"><rect x=".5" y=".5" width="11" height="8"/><path d="M.5 .5L6 5l5.5-4.5"/></svg></div>

    <div class="abs bottom-rule"></div>
    <div class="abs copyright">© 2013 Cadenza Instrument Musical Store. All Rights Reserved.</div>
    <div class="abs footer-links"><span>Home</span><span>Shop</span><span>Sale</span><span>Bog</span><span>Contact Us</span></div>
  </footer>
</div>
</body>
</html>
```